Large Essential oil business needs a unique label design

We offer essential oil blends in various sizes with over 40+ blends. We want a unique design using our new logo.
Classy, easy to read and different than the other EO companies.
With over 40 blends all the ingredients must be l listed.
Warnings: discontinue use if irritation occurs, keep out of reach of children, for external use only unless working with a professional.
Certified Organic and Wild Harvested Essential Oils from all over the world. Pure therapeutic grade.
Would like area for bar code or bar code information if possible...
(see pictures)
5 ml roll on 3 cm H 6 cm Diameter
10 ml roll 4 cm H 6.75 diameter
30 ml roll 4 cm H 10.25 diameter

Diffuser bottles
5 ml 2.25 H 7.5 cm D
10 ml 2.25 H 8.25 D
30 ml 4 cm H 10.25 D

Target Market(s)

retail, health and wellness, all audiences.

Industry/Entity Type

Health And Wellness

Contact Information for Business Card

daphne orlett founder/blender
Kimberley/Fernie, B.C. Canada mistwillowbrook@examplemail.com
(250)381 6094
mistwillowbrook.example

Font styles to use
Decorative

Colors
ec1f27

Requirements
Must have
• Blend name, all ingredients, warnings, instructions, logo,
• 5 ml/.17 fl oz
• 10 ml/.33 fl oz
• 30 ml/1 fl oz
• EXAMPLE BLEND:
• Calm Harbor
• Sleep and Insomnia
• Organic & Wild Crafted Oils of: orange, marjoram, clary sage, melissa, in olive oil
• Usage: roll on soles of feet prior to bed or as needed. Top of shoulders/navel area.
• Discontinue use if irritation occurs, keep out of reach of children, for external use only unless working with a qualified professional.
• Organic and Wild Harvested Oils sourced Globally. 100% Therapeutic Grade
Nice to have
• wood design somehow, unique

```html
<!DOCTYPE html>
<html lang="en">
<head>
<meta charset="utf-8">
<title>Calm Harbor – Roll-on Label</title>
<link href="https://fonts.googleapis.com/css2?family=Jost:wght@300;400&display=swap" rel="stylesheet">
<style>
  :root {
    --page: #f3f3f3;
    --wood-light: #f4f4f4;
    --wood-mid: #e3e3e3;
    --plank-line: rgba(150,150,150,0.35);
    --brand: #c8184f;
    --ink: #2b2b2b;
    --paper: #ffffff;
    --flora-a: #d6d6d6;
    --flora-b: #b9b9b9;
  }
  * { box-sizing: border-box; margin: 0; padding: 0; }
  html, body { width: 1200px; height: 580px; overflow: hidden; }
  body {
    background: radial-gradient(ellipse at center, #ffffff 0%, var(--page) 70%, #e6e6e6 100%);
    font-family: "Jost", sans-serif;
    font-weight: 300;
    color: var(--ink);
    position: relative;
  }
  .label {
    position: absolute; left: 172px; top: 76px; width: 854px; height: 428px;
    background:
      repeating-linear-gradient(90deg, transparent 0 54px, var(--plank-line) 54px 55px, transparent 55px 92px),
      linear-gradient(90deg, var(--wood-mid), var(--wood-light) 30%, var(--wood-mid) 55%, var(--wood-light) 80%, var(--wood-mid));
    overflow: hidden;
  }
  .flora {
    position: absolute; left: 0; right: 0; top: 328px; height: 78px;
    background: linear-gradient(180deg, rgba(214,214,214,0) 0%, var(--flora-a) 45%, var(--flora-b) 100%);
    opacity: 0.7;
  }
  .edge-line { position: absolute; left: 0; top: 404px; width: 100%; height: 8px; }
  .ingredients { position: absolute; left: 30px; top: 79px; width: 290px; font-size: 13px; line-height: 1.45; }
  .usage { position: absolute; left: 30px; top: 135px; width: 290px; font-size: 13px; line-height: 1.45; }
  .sourcing { position: absolute; left: 80px; top: 190px; width: 170px; font-size: 11.5px; line-height: 1.4; text-align: center; font-weight: 400; }
  .barcode-area { position: absolute; left: 30px; top: 236px; width: 148px; height: 82px; background: var(--paper); }
  .grade { position: absolute; left: 240px; top: 250px; width: 80px; font-size: 12.5px; line-height: 1.3; text-align: center; font-weight: 400; }
  .brand {
    position: absolute; left: 378px; top: 40px; height: 340px; width: 62px;
    display: flex; flex-direction: row; justify-content: center; gap: 4px;
    color: var(--brand); font-weight: 400;
  }
  .brand span {
    writing-mode: vertical-rl; transform: rotate(180deg);
    text-align: center; white-space: nowrap;
  }
  .brand .brand-name { font-size: 19px; letter-spacing: 1.5px; }
  .brand .brand-sub { font-size: 9.5px; letter-spacing: 3px; }
  .purity {
    position: absolute; left: 442px; top: 100px; height: 220px;
    writing-mode: vertical-rl; transform: rotate(180deg);
    font-size: 12px; text-align: center;
  }
  .name-band {
    position: absolute; left: 458px; top: 0; width: 44px; height: 100%;
    background: var(--brand); color: #fff;
  }
  .blend-name {
    position: absolute; left: 0; top: 50px; width: 44px; height: 250px;
    writing-mode: vertical-rl; transform: rotate(180deg);
    font-size: 26px; letter-spacing: 7px; text-align: center; white-space: nowrap;
  }
  .volume { position: absolute; left: 4px; top: 386px; font-size: 12px; }
  .caution { position: absolute; left: 576px; top: 40px; width: 236px; font-size: 13.5px; line-height: 1.45; }
  .caution p + p { margin-top: 8px; }
  .caution .first { text-align: justify; letter-spacing: 0.8px; }
  .format-tag { position: absolute; left: 0; width: 1200px; top: 522px; text-align: center; font-family: "Jost", sans-serif; font-weight: 400; font-size: 32px; color: #111; }
</style>
</head>
<body>
  <section class="label">
    <div class="flora" role="img" aria-label="Line-drawn botanical border of leaves and wildflowers"></div>
    <svg class="edge-line" viewBox="0 0 854 8" preserveAspectRatio="none" aria-hidden="true">
      <line x1="0" y1="2" x2="854" y2="2" stroke="#7a7a7a" stroke-width="1"/>
    </svg>

    <p class="ingredients">Organic &amp; wild crafted oils of: orange, marjoram, clary sage, melissa, in olive oil</p>
    <p class="usage">Usage: roll on soles of feet prior to bed or as needed. Top of shoulders/navel area.</p>
    <p class="sourcing">Organic and Wild Harvested Oils sourced Globally</p>
    <div class="barcode-area" aria-label="Barcode area"></div>
    <p class="grade">100% Pure Therapeutic Grade.</p>

    <div class="brand">
      <span class="brand-name">MISTWILLOW BROOK</span>
      <span class="brand-sub">ESSENTIAL OIL CO.</span>
    </div>
    <p class="purity">100% Pure Oil</p>

    <div class="name-band">
      <h1 class="blend-name" style="font-weight:300">Calm Harbor</h1>
      <span class="volume">15ml</span>
    </div>

    <div class="caution">
      <p class="first">Discontinue use if irritation occurs, keep out of reach of children, for external use only unless working with a qualified professional.</p>
      <p>Warnings: discontinue use if irritation occurs, keep out of reach of children, for external use only unless working with a professional.</p>
    </div>
  </section>
  <p class="format-tag">ROLL</p>
</body>
</html>
```